Birch Hauling Business Card Design Project

We need a new company business card. We provide professional timber harvesting (logging) and forest management services. I'm open to any creative design. Most company caps and shirts are navy blue and Light grey. Logo does not necessarily have to contain those colors. Logo containing picture of logging equipment, log truck, trees, or logs are acceptable. Be creative. Final logo should communicate our company's pride and professionalism in the East Texas Timber Industry.
Updates

Target Market(s)

Timber owners, sawmills, and forestry professionals

Industry/Entity Type

Business

Requirements
Must have
• Must have Contact Info.
Phone: 936-402-5917
address: PO Box 4830
Cedar Hollow, Tx 77390
www.jmbirchhauling.example
jmbirchhauling@mailbox.example
Owner: Jared Marsh

Or design must leave room for this info.

```html
<!DOCTYPE html>
<html lang="en">
<head>
<meta charset="utf-8">
<title>Birch Hauling Business Card</title>
<link href="https://fonts.googleapis.com/css2?family=Lato:wght@400;700;900&display=swap" rel="stylesheet">
<style>
  :root {
    --navy: #413d94;
    --navy-dark: #2e2a7a;
    --grey: #8a8a8a;
    --grey-text: #6f6f6f;
    --white: #ffffff;
    --backdrop: #e9e7e4;
  }
  * { margin: 0; padding: 0; box-sizing: border-box; }
  html, body { width: 1200px; height: 960px; overflow: hidden; }
  body {
    position: relative;
    background: var(--backdrop);
    font-family: "Lato", Arial, sans-serif;
  }
  .card {
    position: absolute;
    left: 270px;
    width: 645px;
    height: 368px;
    box-shadow: 0 4px 10px rgba(0,0,0,0.25);
    overflow: hidden;
  }
  /* Front */
  .card-front { top: 84px; background: var(--navy); }
  .front-wordmark {
    position: absolute;
    left: 0; right: 0; top: 155px;
    text-align: center;
    color: var(--white);
    font-weight: 900;
    font-size: 72px;
    line-height: 1;
    letter-spacing: -1px;
  }
  .front-web {
    position: absolute;
    left: 117px; right: 118px; top: 259px;
    display: flex; align-items: center; gap: 8px;
    color: var(--white);
    font-size: 13px;
    letter-spacing: 1.4px;
    white-space: nowrap;
  }
  .front-web .rule {
    flex: 1; height: 2px;
    background: linear-gradient(90deg, rgba(255,255,255,0), var(--white));
  }
  .front-web .rule-right {
    background: linear-gradient(90deg, var(--white), rgba(255,255,255,0));
  }
  /* Back */
  .card-back { top: 507px; background: var(--white); }
  .brand {
    position: absolute;
    top: 66px; left: 0; width: 645px;
  }
  .brand-name {
    position: absolute;
    right: 341px; top: 3px;
    color: var(--navy);
    font-weight: 900;
    font-size: 22px;
    white-space: nowrap;
  }
  .brand-divider {
    position: absolute;
    left: 317px; top: 0; width: 1px; height: 36px;
    background: var(--grey-text);
  }
  .brand-company {
    position: absolute; left: 329px; top: 0;
    color: var(--grey-text); font-weight: 700; font-size: 15px;
  }
  .brand-slogan {
    position: absolute; left: 329px; top: 19px;
    color: var(--grey-text); font-size: 15px;
  }
  .person {
    position: absolute;
    right: 418px; top: 215px;
    text-align: right;
  }
  .person-name { color: var(--navy-dark); font-weight: 700; font-size: 19px; line-height: 22px; }
  .person-title { color: var(--grey-text); font-size: 15px; line-height: 16px; }
  .column-rule {
    position: absolute;
    left: 322px; top: 150px; width: 2px; height: 155px;
    background: linear-gradient(180deg, rgba(120,120,120,0), #777 50%, rgba(120,120,120,0));
  }
  .address {
    position: absolute; left: 372px; top: 171px;
    font-style: normal;
    color: var(--grey-text); font-size: 15px; line-height: 19px;
  }
  .contacts {
    position: absolute; left: 372px; top: 230px;
    list-style: none;
    color: var(--grey-text); font-size: 15px; line-height: 18.5px;
  }
  .contacts li { display: flex; align-items: center; gap: 9px; }
  .contacts svg { width: 18px; height: 14px; flex: none; }
  .back-swoosh { position: absolute; left: 0; top: 0; }
</style>
</head>
<body>
  <section class="card card-front">
    <div class="front-wordmark">Birch Hauling</div>
    <div class="front-web">
      <span class="rule"></span>
      <span>www.jmbirchhauling.example</span>
      <span class="rule rule-right"></span>
    </div>
  </section>

  <section class="card card-back">
    <svg class="back-swoosh" width="645" height="368" viewBox="0 0 645 368">
      <path d="M0,278 Q330,392 645,318 L645,368 L0,368 Z" fill="var(--navy)"/>
      <path d="M150,320 Q420,356 645,290 L645,297 Q430,365 150,320 Z" fill="var(--grey)"/>
    </svg>

    <div class="brand">
      <span class="brand-name">Birch Hauling</span>
      <span class="brand-divider"></span>
      <span class="brand-company">Company Name</span>
      <span class="brand-slogan">Your Slogan</span>
    </div>

    <div class="person">
      <div class="person-name">Jared Marsh</div>
      <div class="person-title">Owner</div>
    </div>

    <div class="column-rule"></div>

    <address class="address">
      PO Box 4830<br>Cedar Hollow, Tx 77390
    </address>

    <ul class="contacts">
      <li>
        <svg viewBox="0 0 18 14"><path d="M2,5 Q9,0 16,5 L14,7 L12,5 L6,5 L4,7 Z M5,7 L13,7 L15,13 L3,13 Z" fill="var(--navy)"/><circle cx="9" cy="10" r="1.8" fill="var(--white)"/></svg>
        <span>936-402-5917</span>
      </li>
      <li>
        <svg viewBox="0 0 18 14"><rect x="1" y="1" width="16" height="12" fill="var(--navy)"/><path d="M1.5,1.5 L9,8 L16.5,1.5" stroke="var(--white)" stroke-width="1.3" fill="none"/></svg>
        <span>jmbirchhauling@mailbox.example</span>
      </li>
      <li>
        <svg viewBox="0 0 18 14"><rect x="2" y="1" width="14" height="9" fill="none" stroke="var(--navy)" stroke-width="1.8"/><rect x="8" y="10" width="2" height="2" fill="var(--navy)"/><rect x="5" y="12" width="8" height="1.6" fill="var(--navy)"/></svg>
        <span>www.jmbirchhauling.example</span>
      </li>
    </ul>
  </section>
</body>
</html>
```